Wandering Rooms Stationary Set

Wandering Rooms is a bespoke interior design firm set to provide services to VIP clients with elegance and minimalism is the main theme for our stationary set. We require a full stationary set covering A4 letterhead, A4 & A3 envelopes, business cards, USB's, CDs, email signature and any other item the designer sees fit. logo is already designed and finalized, and we require the designer to use it as is without modifying the logo.

Address to be used on letterhead / business cards ...etc shall be as follows:

Phone : +971 2 518 2047
P.O. Box : 309186
Address: Block C&D, Bldg. 47, Court 12, Abu Dhabi, United Arab Emirates
Website: www.wanderingrooms-example.com

Target Market(s)

VIP Clients

Industry/Entity Type

Interior Design

Font styles to use
Other font styles liked:
• something to be unique

Colors

Designer to choose colors to be used in the design.

Requirements
Must have
• Elegant, minimalistic
Nice to have
• Simple yet elegant design having a sharp yet clean cut format
Should not have
• No additional colours, just colours that are used in the logo (silver, black or gold)

```html
<!DOCTYPE html>
<html lang="en">
<head>
<meta charset="utf-8">
<title>Wandering Rooms Business Card</title>
<link rel="stylesheet" href="https://fonts.googleapis.com/css2?family=Cormorant+Garamond:wght@400;500;700&display=swap">
<style>
  :root {
    --backdrop: #2b2420;
    --card: #1f1f20;
    --gold: #c9a227;
    --gold-soft: #b8952a;
    --white: #f2f2f2;
  }
  * { margin: 0; padding: 0; box-sizing: border-box; }
  html, body { width: 1200px; height: 715px; overflow: hidden; }
  body {
    background: var(--backdrop);
    font-family: "Cormorant Garamond", Georgia, serif;
    position: relative;
  }
  .card {
    position: absolute;
    top: 210px;
    width: 520px;
    height: 297px;
    background: var(--card);
    box-shadow: 0 14px 30px rgba(0,0,0,0.45);
  }
  .card--front { left: 50px; }
  .card--back { left: 630px; }

  .wordmark {
    color: var(--gold);
    font-weight: 500;
    text-align: center;
    line-height: 1;
  }
  .card--front .wordmark {
    position: absolute;
    top: 100px; left: 0; right: 0;
    font-size: 44px;
    letter-spacing: 1px;
  }
  .card--front .website {
    position: absolute;
    top: 215px; left: 0; right: 0;
    text-align: center;
    color: var(--gold-soft);
    font-size: 14px;
    letter-spacing: 1.5px;
  }

  .card--back .wordmark {
    position: absolute;
    top: 112px; left: 20px;
    width: 250px;
    font-size: 34px;
  }
  .divider {
    position: absolute;
    left: 290px; top: 70px;
    width: 2px; height: 122px;
    background: var(--white);
  }
  .contact {
    position: absolute;
    left: 308px; top: 72px;
    color: var(--white);
  }
  .contact__name {
    color: var(--gold);
    font-weight: 700;
    font-size: 19px;
    letter-spacing: 0.5px;
  }
  .contact__title { font-size: 15px; margin-bottom: 16px; }
  .contact__list { list-style: none; font-size: 13px; line-height: 1.5; }
  .contact__list li { display: flex; align-items: center; gap: 8px; }
  .contact__icon {
    width: 16px; height: 16px; flex: none;
  }
  .contact__spacer { width: 16px; flex: none; }
  .address {
    position: absolute;
    left: 0; right: 0; bottom: 32px;
    text-align: center;
    color: var(--white);
    font-weight: 700;
    font-size: 15px;
  }
</style>
</head>
<body>
  <section class="card card--front">
    <div class="wordmark">Wandering Rooms</div>
    <div class="website">www.wanderingrooms-example.com</div>
  </section>

  <section class="card card--back">
    <div class="wordmark">Wandering Rooms</div>
    <div class="divider"></div>
    <div class="contact">
      <div class="contact__name">Layla Haddad</div>
      <div class="contact__title">Director</div>
      <ul class="contact__list">
        <li>
          <svg class="contact__icon" viewBox="0 0 16 16" aria-hidden="true">
            <circle cx="8" cy="8" r="8" fill="#f2f2f2"/>
            <path d="M5 4.5h2l.6 2-1 .8a5 5 0 0 0 2.1 2.1l.8-1 2 .6v2c-3.8.3-6.8-2.7-6.5-6.5z" fill="#1f1f20"/>
          </svg>
          +971 2 518 2047
        </li>
        <li>
          <svg class="contact__icon" viewBox="0 0 16 16" aria-hidden="true">
            <circle cx="8" cy="8" r="8" fill="#f2f2f2"/>
            <rect x="4" y="5" width="8" height="6" fill="#1f1f20"/>
            <path d="M4 5l4 3.3L12 5" stroke="#f2f2f2" stroke-width="0.8" fill="none"/>
          </svg>
          layla@wanderingrooms-example.com
        </li>
        <li>
          <svg class="contact__icon" viewBox="0 0 16 16" aria-hidden="true">
            <circle cx="8" cy="8" r="8" fill="#f2f2f2"/>
            <path d="M8 3.5a3 3 0 0 1 3 3c0 2.2-3 6-3 6s-3-3.8-3-6a3 3 0 0 1 3-3z" fill="#1f1f20"/>
            <circle cx="8" cy="6.5" r="1" fill="#f2f2f2"/>
          </svg>
          P.O. Box : 309186
        </li>
      </ul>
    </div>
    <div class="address">Block C&amp;D, Bldg. 47, Court 12, Abu Dhabi, United Arab Emirates</div>
  </section>
</body>
</html>
```